Creative, fresh business card design for Ripplecraft Facades

We need a fresh, creative business card design for Ripplecraft Facades. We are the manufacturer of Ripplecraft Facades in Australia. Wall panels are 2400 x 1200mm panels made from MDF and feature 3D patterns on the face of the panel. The colours to be used are green, silver/grey and white RGB
Red 187
Green 207
Blue 65.

An idea is to possibly use a watermark of one of our designs as a background (like on the "Grids" design on the left hand side of page 2 of our brochure).

Target Market(s)

Interior designers, architects, builders and home renovators

Industry/Entity Type

Business

Contact Information for Business Card

Details to go on the card are:
Our logo (attached),
Slogan: "Decorative panels for interiors and exteriors",
Contact name,
Position,
Mobile phone number,
Business address,
Business phone,
Business fax,
Website and
Email address.

I have attached a few images of our panels and our brochure for reference.

The colours of the business card should feature our logo colours which are: RGB
Red 187
Green 207
Blue 65

Requirements
Must have
• Very modern fonts and design. Some of the designs shown especially the "Prisms" design which is a popular design.
Nice to have
• Creative but simple design. Very contemporary.
Should not have
• Anything ornate or old fashioned.

```html
<!DOCTYPE html>
<html lang="en">
<head>
<meta charset="utf-8">
<title>Ripplecraft Facades – Business Card</title>
<link rel="stylesheet" href="https://fonts.googleapis.com/css2?family=Oswald:wght@600&family=Exo+2:wght@400;500&display=swap">
<style>
  :root {
    --page: #2a2a2a;
    --card-top: #222222;
    --card-bottom: #141414;
    --lime: #bbcf41;
    --silver: #b8b8b8;
    --grey: #8a8a8a;
    --white: #f4f4f4;
  }
  html, body {
    margin: 0;
    width: 1200px;
    height: 1000px;
    overflow: hidden;
    background: var(--page);
  }
  .card {
    position: absolute;
    left: 150px;
    top: 240px;
    width: 900px;
    height: 520px;
    border-radius: 34px;
    overflow: hidden;
    background: linear-gradient(160deg, var(--card-top), var(--card-bottom));
    box-shadow: 0 20px 50px rgba(0,0,0,.45);
    font-family: "Exo 2", sans-serif;
    color: var(--white);
  }
  .card__texture {
    position: absolute;
    inset: 0;
    background: radial-gradient(ellipse at 60% 40%, rgba(255,255,255,.05), rgba(255,255,255,0) 70%);
  }
  .brand {
    position: absolute;
    left: 530px;
    top: 92px;
    display: flex;
    align-items: flex-start;
    gap: 14px;
  }
  .brand__square {
    width: 58px;
    height: 58px;
    background: var(--lime);
  }
  .brand__name {
    font-size: 27px;
    font-weight: 400;
    color: var(--silver);
    line-height: 1;
    margin: 2px 0 8px;
  }
  .brand__tagline {
    font-size: 14px;
    letter-spacing: 1.5px;
    color: var(--grey);
    line-height: 1.2;
    width: 230px;
  }
  .person {
    position: absolute;
    left: 110px;
    top: 218px;
  }
  .person__name {
    font-family: "Oswald", sans-serif;
    font-weight: 600;
    font-size: 44px;
    letter-spacing: 1px;
    text-transform: uppercase;
    margin: 0;
    line-height: 1;
  }
  .person__role {
    font-size: 21px;
    color: var(--lime);
    margin-top: 8px;
    line-height: 1;
  }
  .divider {
    position: absolute;
    left: 210px;
    right: 0;
    top: 290px;
    height: 2px;
    background: var(--lime);
  }
  .contacts {
    position: absolute;
    left: 110px;
    top: 322px;
    margin: 0;
    padding: 0;
    list-style: none;
  }
  .contacts li {
    display: flex;
    align-items: center;
    gap: 22px;
    height: 36px;
    font-size: 22px;
  }
  .contacts svg {
    width: 20px;
    height: 20px;
    flex: none;
  }
  .contacts .accent { color: var(--lime); }
  .address {
    position: absolute;
    right: 60px;
    bottom: 70px;
    text-align: right;
    font-size: 20px;
    line-height: 1.4;
    letter-spacing: .5px;
  }
</style>
</head>
<body>
  <div class="card">
    <div class="card__texture" role="img" aria-label="Faint hexagonal panel pattern across the card"></div>

    <div class="brand">
      <div class="brand__square"></div>
      <div>
        <div class="brand__name">Ripplecraft Facades</div>
        <div class="brand__tagline">decorative panels for interiors &amp; landscapes</div>
      </div>
    </div>

    <div class="person">
      <h1 class="person__name">Daniel Hart</h1>
      <div class="person__role">Director</div>
    </div>
    <div class="divider"></div>

    <ul class="contacts">
      <li>
        <svg viewBox="0 0 20 20" fill="none" stroke="#bbcf41" stroke-width="2"><rect x="5" y="1" width="10" height="18" rx="2"/><line x1="9" y1="15.5" x2="11" y2="15.5"/></svg>
        <span>+000 321 654 987</span>
      </li>
      <li>
        <svg viewBox="0 0 20 20" fill="#bbcf41"><path d="M4 2l4 1 1 4-2 2c1 2 3 4 5 5l2-2 4 1 1 4-2 2C9 19 1 11 2 4z"/></svg>
        <span>+000 321 654 988</span>
      </li>
      <li>
        <svg viewBox="0 0 20 20" fill="#bbcf41"><rect x="5" y="1" width="10" height="6"/><rect x="1" y="8" width="18" height="8" rx="1"/><rect x="5" y="13" width="10" height="6" fill="#1a1a1a" stroke="#bbcf41" stroke-width="1.5"/></svg>
        <span>+000 321 654 989</span>
      </li>
      <li>
        <svg viewBox="0 0 20 20" fill="#bbcf41"><path d="M1 4h18v12H1z"/><path d="M1 4l9 7 9-7" fill="none" stroke="#1a1a1a" stroke-width="1.5"/></svg>
        <span>hello@ripplecraft.com</span>
      </li>
      <li>
        <svg viewBox="0 0 20 20" fill="none" stroke="#bbcf41" stroke-width="2.4"><circle cx="11" cy="8" r="6"/><line x1="7" y1="12.5" x2="2" y2="18"/></svg>
        <span>www.<span class="accent">ripplecraftfacades</span>.com</span>
      </li>
    </ul>

    <div class="address">
      14 Kestrel Lane<br>
      Brookvale, 2100
    </div>
  </div>
</body>
</html>
```